Slogan
Zielgruppe
Wir sind ein Familienhotel in Österreich. Unsere Zielgruppe sind Familien und auch Paare. Unsere Hauptthemen sind im Sommer wandern und im Winter skifahren.
Aufgabenstellung
Es soll aus dem Claim hervorgehen, dass wir besonders Familien ansprechen. Wir sind jedoch kein reines Kinderhotel. Es sind bei uns auch Paare willkommen.

```html
<!DOCTYPE html>
<html lang="de">
<head>
<meta charset="utf-8">
<title>Slogan – Familienhotel</title>
<link rel="stylesheet" href="https://fonts.googleapis.com/css2?family=Arimo:wght@400&display=swap">
<style>
  :root {
    --bg: #ffffff;
    --slogan-blue: #1a8fc4;
  }
  html, body {
    margin: 0;
    padding: 0;
    width: 1200px;
    height: 1200px;
    overflow: hidden;
    background: var(--bg);
  }
  .canvas {
    position: relative;
    width: 1200px;
    height: 1200px;
    background: var(--bg);
  }
  .slogan {
    position: absolute;
    left: 0;
    right: 0;
    top: 564px;
    margin: 0;
    text-align: center;
    font-family: "Arimo", Arial, sans-serif;
    font-weight: 400;
    font-size: 39px;
    line-height: 1.2;
    color: var(--slogan-blue);
    white-space: nowrap;
  }
</style>
</head>
<body>
  <main class="canvas">
    <p class="slogan">Weil bei uns Familien und Paare willkommen sind</p>
  </main>
</body>
</html>
```